We are a recruitment company based in Norwich/Cambridge England.
I have included our company logo which we want to remain the same.

What we are looking for is a new creative Business card which will really stand out!!

Contact Information for Business Card

Harriet Dunmore
email: Harriet@plavex.co.uk
Address: Brackwell House
Fenmoor Enterprise Park
Partridge Way
Norwich
QB9 3KX
Tel:01632 960418

```html
<!DOCTYPE html>
<html lang="en">
<head>
<meta charset="utf-8">
<title>Plavex Business Card</title>
<link href="https://fonts.googleapis.com/css2?family=Roboto:wght@400;500&display=swap" rel="stylesheet">
<style>
  :root {
    --backdrop: #2b2b2b;
    --card: #1a1a1a;
    --lime: #7dd13a;
    --white: #f2f2f2;
    --grey: #9a979c;
  }
  * { box-sizing: border-box; margin: 0; padding: 0; }
  html, body {
    width: 1200px;
    height: 900px;
    overflow: hidden;
    background: var(--backdrop);
    font-family: "Roboto", Arial, sans-serif;
  }
  .stage {
    position: relative;
    width: 1200px;
    height: 900px;
  }
  .card {
    position: absolute;
    left: 240px;
    width: 720px;
    height: 400px;
    background: var(--card);
    border-bottom: 5px solid var(--lime);
    box-shadow: 0 12px 30px rgba(0,0,0,0.45);
  }
  .card--front { top: 30px; }
  .card--back  { top: 470px; }

  .brand {
    display: flex;
    align-items: center;
    gap: 14px;
    color: var(--lime);
    font-weight: 500;
    letter-spacing: 0.5px;
  }
  .brand__dot {
    border-radius: 50%;
    background: var(--lime);
  }
  .card--front .brand {
    position: absolute;
    left: 50%;
    top: 50%;
    transform: translate(-50%, -55%);
    font-size: 62px;
  }
  .card--front .brand__dot { width: 54px; height: 54px; }

  .card--back .brand {
    position: absolute;
    left: 60px;
    top: 160px;
    font-size: 44px;
  }
  .card--back .brand__dot { width: 40px; height: 40px; }

  .divider {
    position: absolute;
    left: 372px;
    top: 95px;
    width: 2px;
    height: 180px;
    background: var(--lime);
  }
  .contact {
    position: absolute;
    left: 408px;
    top: 88px;
    color: var(--white);
  }
  .contact__name {
    color: var(--lime);
    font-size: 25px;
    font-weight: 500;
    letter-spacing: 1.5px;
    text-transform: uppercase;
    margin-bottom: 14px;
  }
  .contact__address {
    font-style: normal;
    font-size: 18px;
    line-height: 21px;
    margin-bottom: 12px;
  }
  .contact__list { list-style: none; }
  .contact__item {
    display: flex;
    align-items: center;
    gap: 10px;
    font-size: 18px;
    line-height: 23px;
  }
  .contact__icon {
    width: 15px;
    height: 15px;
    flex: none;
  }
  .contact__domain { color: var(--lime); }
</style>
</head>
<body>
<main class="stage">

  <section class="card card--front" aria-label="Card front">
    <div class="brand">
      <span class="brand__dot"></span>
      <span class="brand__name">Plavex</span>
    </div>
  </section>

  <section class="card card--back" aria-label="Card back">
    <div class="brand">
      <span class="brand__dot"></span>
      <span class="brand__name">Plavex</span>
    </div>

    <div class="divider"></div>

    <div class="contact">
      <h1 class="contact__name">Harriet Dunmore</h1>
      <address class="contact__address">
        Brackwell House<br>
        Fenmoor Enterprise Park<br>
        Partridge Way Norwich<br>
        QB9 3KX
      </address>
      <ul class="contact__list">
        <li class="contact__item">
          <svg class="contact__icon" viewBox="0 0 16 16" aria-hidden="true">
            <rect x="0" y="0" width="16" height="16" rx="2" fill="#7dd13a"/>
            <path d="M5 3.5c-.8.4-1.4 1.3-1 2.6.8 2.6 2.9 4.9 5.6 5.9 1.2.4 2.1-.2 2.6-1l-1.8-1.4-1 .8c-1.2-.6-2.2-1.6-2.8-2.8l.8-1z" fill="#1a1a1a"/>
          </svg>
          01632 960418
        </li>
        <li class="contact__item">
          <svg class="contact__icon" viewBox="0 0 16 16" aria-hidden="true">
            <rect x="1" y="3" width="14" height="10" fill="#7dd13a"/>
            <path d="M1 3l7 6 7-6" fill="none" stroke="#1a1a1a" stroke-width="1.4"/>
          </svg>
          Harriet@plavex.co.uk
        </li>
        <li class="contact__item">
          <svg class="contact__icon" viewBox="0 0 16 16" aria-hidden="true">
            <circle cx="8" cy="8" r="7" fill="#7dd13a"/>
            <ellipse cx="8" cy="8" rx="3" ry="7" fill="none" stroke="#1a1a1a" stroke-width="1.2"/>
            <path d="M1 8h14" stroke="#1a1a1a" stroke-width="1.2"/>
          </svg>
          <span>www.<span class="contact__domain">plavex</span>.co.uk</span>
        </li>
      </ul>
    </div>
  </section>

</main>
</body>
</html>
```